The Linen Loft Co

We need a business card design for our wardrobe company.
Please visit our website www.gentlelinenlofts.com to get an idea of who we are.

```html
<!DOCTYPE html>
<html lang="en">
<head>
<meta charset="UTF-8">
<title>The Linen Loft Co – Business Card</title>
<link href="https://fonts.googleapis.com/css2?family=Roboto:wght@400;500;700&display=swap" rel="stylesheet">
<style>
  :root {
    --backdrop: #e4e4e4;
    --card-white: #ffffff;
    --card-black: #000000;
    --ink-dark: #111111;
    --ink-light: #ffffff;
  }
  html, body {
    margin: 0;
    padding: 0;
    width: 1200px;
    height: 989px;
    overflow: hidden;
    background: var(--backdrop);
    font-family: "Roboto", Arial, sans-serif;
  }
  .business-card {
    position: absolute;
    left: 164px;
    top: 227px;
    width: 884px;
    height: 510px;
    background: var(--card-white);
    overflow: hidden;
  }
  .card-shape {
    position: absolute;
    inset: 0;
    width: 884px;
    height: 510px;
  }
  .brand-square {
    position: absolute;
    left: 78px;
    top: 226px;
    width: 56px;
    height: 56px;
    border: 3px solid var(--ink-dark);
    box-sizing: border-box;
  }
  .brand-text {
    position: absolute;
    left: 200px;
    top: 227px;
    width: 225px;
    display: flex;
    flex-direction: column;
    align-items: center;
    color: var(--ink-dark);
  }
  .brand-name {
    font-size: 19px;
    font-weight: 500;
    text-transform: uppercase;
    letter-spacing: 0.2px;
    line-height: 24px;
    white-space: nowrap;
  }
  .brand-tagline {
    font-size: 16px;
    font-weight: 500;
    line-height: 22px;
    margin-top: 4px;
    white-space: nowrap;
  }
  .contact {
    position: absolute;
    right: 42px;
    top: 146px;
    text-align: right;
    color: var(--ink-light);
  }
  .person-name {
    font-size: 36px;
    font-weight: 700;
    line-height: 42px;
    margin: 0;
  }
  .person-role {
    font-size: 22px;
    font-weight: 500;
    line-height: 26px;
    margin: 0 0 20px;
  }
  .contact-line {
    font-size: 22px;
    font-weight: 400;
    line-height: 27px;
    margin: 0;
    white-space: nowrap;
  }
  .address { margin-bottom: 11px; }
</style>
</head>
<body>
  <div class="business-card">
    <svg class="card-shape" viewBox="0 0 884 510" aria-hidden="true">
      <path d="M360 0 C 490 90 545 280 380 510 L884 510 L884 0 Z" fill="var(--card-black)"/>
      <path d="M384 2 C 512 92 568 285 404 510" fill="none" stroke="var(--ink-light)" stroke-width="1.8"/>
    </svg>

    <div class="brand-square"></div>
    <div class="brand-text">
      <span class="brand-name">The Linen Loft Co</span>
      <span class="brand-tagline">Made to Fit Every Home</span>
    </div>

    <div class="contact">
      <p class="person-name">Daniel Hartley</p>
      <p class="person-role">President</p>
      <div class="address">
        <p class="contact-line">Marlow House, 42 Ashby Lane</p>
        <p class="contact-line">London N4 7QT</p>
      </div>
      <p class="contact-line">020 7946 0318</p>
      <p class="contact-line">info@gentlelinenlofts.com</p>
      <p class="contact-line">www.gentlelinenlofts.com</p>
    </div>
  </div>
</body>
</html>
```